Web Site Design for a Finance (lending) Company

We are opening a new subsidiary that focuses on lending money in the real estate industry. We need a web site designed to represent the business.

The business is lending money to real estate investors. A typical client/borrower will be looking to borrow money to buy a house, renovate it and then sell it at a profit, all within 12 months or less.

Company name is RTV Finance. Our logo is attached.

Attached is a general outline for the web site. We're working on writing more text for each page but this should give you enough to get started with some ideas.

Competitor web site that I like a lot (as an example): https://dorvaleqcapital.example/. Many of the general items on this site match what we will need (description of loan programs, FAQ)

Target Market(s)

Real estate investors (generally individuals or small companies with just a few people) who are buying homes, renovating them and then selling them at a profit.

Industry/Entity Type

Finance

Coding

Coded - Design and coding required

Number of Pages Required

5+ page

Colors

Designer to choose colors to be used in the design.

Requirements
Must have
• Minimalist design. Clean lines without too much clutter. Some stock photography is ok but the photos should not be distracting. They should almost fade in to the background so that user can focus on the key information about what our company does instead. We are a finance company, not a design company, so the information about our products will be more interesting to site visitors than the art.
• Some minimalist examples from Snapboard:
• https://www.snapboardia.example/explore/minimalist-web-design/
Nice to have
• If you search in zoovle for "hard money lenders" you will find many examples of web sites from our competition. I have provided a link above to competitor web site that I like a lot.
• I have attached our logo in EPS format. Logo is green. Web site doesn't have to be green but it should be of a color that will work well with the logo.

```html
<!DOCTYPE html>
<html lang="en">
<head>
<meta charset="utf-8">
<title>RTV Finance — Local Real Estate Lending</title>
<link rel="stylesheet" href="https://fonts.googleapis.com/css2?family=Roboto:wght@300;400;500;700&display=swap">
<style>
:root{
  --green:#0b5a3a;
  --green-dark:#084a30;
  --green-deep:#06402a;
  --ink:#222;
  --text:#666;
  --muted:#999;
  --line:#e3e3e3;
  --paper:#fff;
  --soft:#f4f5f5;
  --footer:#1b1d1b;
  --footer-text:#cfd2cf;
}
*{box-sizing:border-box;margin:0;padding:0}
html,body{width:1200px;height:3543px;overflow:hidden}
body{position:relative;font-family:"Roboto",Arial,sans-serif;color:var(--ink);background:var(--paper)}
a{color:inherit;text-decoration:none}
.abs{position:absolute}

/* header */
.topline{left:0;top:0;width:1200px;height:5px;background:var(--green)}
.brand{left:99px;top:36px;display:flex;align-items:center;gap:12px}
.brand-mark{width:30px;height:30px;background:var(--green)}
.brand-name{font-size:26px;font-weight:500;color:var(--green);line-height:1}
.contact-top{right:99px;top:36px;display:flex;gap:28px;font-size:12px;color:#555;align-items:center}
.contact-top span{display:flex;align-items:center;gap:10px}
.contact-top i{width:32px;height:32px;border:1px solid #ccc;border-radius:50%;display:flex;align-items:center;justify-content:center}
.nav{right:99px;top:92px;display:flex;gap:60px;font-size:13px;font-weight:500;color:#333;text-transform:uppercase}
.nav .active{color:var(--green);border-top:3px solid var(--green);padding-top:4px;margin-top:-7px}

/* hero */
.hero{left:0;top:135px;width:1200px;height:640px;background:linear-gradient(180deg,#9aa3ab 0%,#c9ced3 45%,#e6e8ea 100%)}
.hero-brand{left:0;top:262px;width:1200px;text-align:center;font-size:30px;font-weight:500;color:#fff}
.hero-title{left:0;top:360px;width:1200px;text-align:center;color:#fff;font-size:34px;font-weight:700;line-height:1.35;text-transform:uppercase;text-shadow:0 2px 6px rgba(0,0,0,.35)}
.hero-down{left:586px;top:524px;width:28px;height:46px;border:2px solid #fff;border-radius:14px;display:flex;align-items:center;justify-content:center}
.hero-cut{left:0;top:600px;width:1200px;height:180px}

/* welcome */
.welcome-title{left:0;top:742px;width:1200px;text-align:center;font-size:30px;font-weight:400;color:#222}
.welcome-title b,.section-title b{color:var(--green);font-weight:500}
.welcome-text{left:180px;top:796px;width:840px;text-align:center;font-size:13px;line-height:2;color:var(--text)}
.loan-card{top:881px;width:491px;height:491px;border:1px solid var(--line);background:#fff}
.loan-photo{left:0;top:0;width:489px;height:253px}
.loan-body{left:0;top:355px;width:489px;text-align:center}
.loan-body h3{font-size:17px;font-weight:500;color:#222;text-transform:uppercase;margin-bottom:14px}
.loan-body p{font-size:12px;line-height:1.9;color:var(--text);padding:0 50px}
.loan-body .more{display:inline-block;margin-top:18px;font-size:12px;color:var(--green)}

/* why */
.why{left:0;top:1450px;width:1200px;height:456px;background:linear-gradient(180deg,var(--green) 0%,var(--green-dark) 100%)}
.why-title{left:99px;top:80px;font-size:30px;font-weight:500;color:#fff;text-transform:uppercase}
.feature{width:330px;display:flex;gap:18px;color:#fff}
.feature-icon{flex:0 0 76px;height:76px;border:3px solid #fff;border-radius:50%;display:flex;align-items:center;justify-content:center}
.feature h4{font-size:15px;font-weight:500;text-transform:uppercase;margin:6px 0 10px}
.feature p{font-size:12px;line-height:1.8;color:#e6efe9}

/* blog */
.section-title{left:0;width:1200px;text-align:center;font-size:30px;font-weight:400;color:#222;text-transform:uppercase}
.post{top:2048px;width:321px;height:378px;border:1px solid var(--line);background:#fff}
.post-photo{left:0;top:0;width:319px;height:212px}
.post-body{left:18px;top:232px;width:285px}
.post-body h5{font-size:13px;font-weight:500;text-transform:uppercase;color:#222;margin-bottom:10px}
.post-body p{font-size:12px;line-height:1.8;color:var(--text)}
.post-meta{left:18px;top:336px;font-size:11px;color:#555;display:flex;gap:10px}
.post-meta b{color:var(--green);font-weight:400}
.post-rule{left:18px;top:318px;width:285px;height:1px;background:var(--line)}

/* testimonials */
.clients{left:0;top:2508px;width:1200px;height:560px;background:linear-gradient(180deg,#f7f8f8,#eceeee)}
.clients-sub{left:0;top:2626px;width:1200px;text-align:center;font-size:12px;color:var(--text)}
.quote-box{left:156px;top:2671px;width:888px;height:234px;background:#fff}
.quote-text{left:40px;top:30px;width:808px;text-align:center;font-size:12px;font-style:italic;line-height:2.1;color:#888}
.quote-author{left:320px;top:150px;display:flex;align-items:center;gap:14px}
.avatar{width:58px;height:58px;border-radius:50%;background:linear-gradient(135deg,#8a8f93,#4f5458)}
.quote-author h6{font-size:13px;font-weight:500;color:var(--green);text-transform:uppercase}
.quote-author span{font-size:11px;color:var(--muted)}
.quote-mark{left:774px;top:150px;font-size:70px;line-height:1;color:var(--green);font-weight:700}
.arrow-btn{top:2774px;width:32px;height:32px;border-radius:50%;background:#fff;border:1px solid #ddd;display:flex;align-items:center;justify-content:center}
.dots{left:578px;top:2963px;display:flex;gap:6px}
.dots i{width:10px;height:10px;border-radius:50%;border:1px solid #999}
.dots i.on{background:var(--green);border-color:var(--green)}

/* footer */
.footer{left:0;top:2940px;width:1200px;height:603px;background:linear-gradient(180deg,#252825,var(--footer))}
.footer-cut{left:0;top:2900px;width:1200px;height:160px}
.f-col{top:3160px;color:var(--footer-text);font-size:12px}
.f-col h4{font-size:16px;font-weight:500;color:#fff;text-transform:uppercase;margin-bottom:30px}
.f-list li{list-style:none;display:flex;gap:14px;margin-bottom:18px;line-height:1.7}
.f-links li{list-style:none;margin-bottom:13px}
.f-links li::before{content:"›";margin-right:14px;color:#fff}
.f-input{width:272px;height:40px;background:#fff;padding:0 12px;font-size:11px;color:#aaa;display:flex;align-items:center;margin-top:16px}
.f-btn{width:112px;height:36px;background:#8c918d;color:#fff;font-size:12px;font-weight:500;display:flex;align-items:center;justify-content:center;margin-top:12px}
.f-social{display:flex;align-items:center;gap:14px;margin-bottom:16px}
.f-social i{width:44px;height:44px;border:2px solid #fff;border-radius:50%;display:block}
.f-divider{top:3180px;width:1px;height:180px;background:#555}
.f-rule{left:99px;top:3413px;width:1002px;height:1px;background:#555}
.badges-label{left:99px;top:3470px;font-size:12px;color:#fff;text-transform:uppercase}
.badge{top:3456px;height:44px;background:#d9dcd9}
.copyright{left:640px;top:3470px;font-size:12px;color:var(--footer-text)}
.chat{left:959px;top:3459px;width:141px;height:36px;border-radius:18px;background:var(--green);color:#fff;font-size:12px;font-weight:500;display:flex;align-items:center;justify-content:center;gap:10px}
</style>
</head>
<body>

<!-- header -->
<div class="abs topline"></div>
<div class="abs brand"><span class="brand-mark"></span><span class="brand-name">RTV Finance</span></div>
<div class="abs contact-top">
  <span><i><svg width="14" height="14" viewBox="0 0 24 24"><path fill="#555" d="M6.6 10.8a15 15 0 0 0 6.6 6.6l2.2-2.2a1 1 0 0 1 1-.25 11.4 11.4 0 0 0 3.6.57 1 1 0 0 1 1 1V20a1 1 0 0 1-1 1A17 17 0 0 1 3 4a1 1 0 0 1 1-1h3.5a1 1 0 0 1 1 1c0 1.25.2 2.45.57 3.57a1 1 0 0 1-.25 1z"/></svg></i>CALL US : (555) - 210 - 4480</span>
  <span><i><svg width="14" height="14" viewBox="0 0 24 24"><path fill="#555" d="M3 5h18v14H3zm2 2v.5l7 5 7-5V7l-7 5z"/></svg></i>MAIL US : info@rtvfinance.example</span>
</div>
<nav class="abs nav">
  <a class="active">Home</a><a>About Us</a><a>Loans</a><a>Resources</a><a>Contact Us</a>
</nav>

<!-- hero -->
<div class="abs hero" role="img" aria-label="Soft blurred photo of business people in a bright office with papers on a desk"></div>
<div class="abs hero-brand">RTV Finance</div>
<h1 class="abs hero-title">Local Real Estate Experts Lending<br>to Local Real Estate Investors</h1>
<div class="abs hero-down"><svg width="10" height="16" viewBox="0 0 10 16"><path d="M5 1v12M1 9l4 4 4-4" stroke="#fff" stroke-width="1.6" fill="none"/></svg></div>
<svg class="abs hero-cut" viewBox="0 0 1200 180" preserveAspectRatio="none">
  <polygon points="0,150 600,0 1200,150 1200,180 0,180" fill="var(--green)"/>
  <polygon points="0,172 600,20 1200,172 1200,180 0,180" fill="#fff"/>
</svg>

<!-- welcome -->
<h2 class="abs welcome-title">WELCOME TO <b>RTV FINANCE</b></h2>
<p class="abs welcome-text">RTV Finance is a local business with local knowledge and strong industry relationships. A partner with a wide network who offers value added services. RTV has an established pool of experienced investors available for your real estate investment needs.</p>

<div class="abs loan-card" style="left:97px">
  <div class="abs loan-photo" role="img" aria-label="Photo of a hand holding car keys in front of a car" style="background:linear-gradient(135deg,#6d7073,#b7b9bb)"></div>
  <svg class="abs" style="left:0;top:215px" width="489" height="60" viewBox="0 0 489 60" preserveAspectRatio="none"><polygon points="0,0 244,38 489,0 489,60 0,60" fill="var(--green)"/><polygon points="0,14 244,48 489,14 489,60 0,60" fill="#fff"/></svg>
  <div class="abs loan-body"><h3>Fix and Flip Loans</h3><p>Lorem ipsum dolor sit amet, consectetur adipiscing elit, sed do eiusmod tempor incididunt ut labore et dolore magna aliqu enim ad minim</p><a class="more">Read More »</a></div>
</div>
<div class="abs loan-card" style="left:612px">
  <div class="abs loan-photo" role="img" aria-label="Photo of a handshake over a small model house" style="background:linear-gradient(135deg,#3c4044,#d3d6d8)"></div>
  <svg class="abs" style="left:0;top:215px" width="489" height="60" viewBox="0 0 489 60" preserveAspectRatio="none"><polygon points="0,0 244,38 489,0 489,60 0,60" fill="var(--green)"/><polygon points="0,14 244,48 489,14 489,60 0,60" fill="#fff"/></svg>
  <div class="abs loan-body"><h3>Commercial Hard Money Loans</h3><p>Lorem ipsum dolor sit amet, consectetur adipiscing elit, sed do eiusmod tempor incididunt ut labore et dolore magna aliqu enim ad minim</p><a class="more">Read More »</a></div>
</div>

<!-- why borrow -->
<section class="abs why">
  <h2 class="abs why-title">Why Borrow From RTV</h2>
  <div class="abs feature" style="left:99px;top:160px"><div class="feature-icon"><svg width="30" height="30" viewBox="0 0 24 24" fill="none" stroke="#fff" stroke-width="1.8"><path d="M9 18h6M10 21h4M12 3a6 6 0 0 0-3.5 10.9V16h7v-2.1A6 6 0 0 0 12 3z"/></svg></div><div><h4>Experts</h4><p>Excepteur sint occaecat cupidatat non proidentunt in cucia deserunt.</p></div></div>
  <div class="abs feature" style="left:451px;top:160px"><div class="feature-icon"><svg width="30" height="30" viewBox="0 0 24 24"><path fill="#fff" d="M13 2 4 14h6l-1 8 9-12h-6z"/></svg></div><div><h4>Fast Approval</h4><p>Excepteur sint occaecat cupidatat non proidentunt in cucia deserunt.</p></div></div>
  <div class="abs feature" style="left:801px;top:160px"><div class="feature-icon"><svg width="30" height="30" viewBox="0 0 24 24"><circle cx="12" cy="8" r="4" fill="#fff"/><path fill="#fff" d="M4 21a8 8 0 0 1 16 0z"/></svg></div><div><h4>Professional</h4><p>Excepteur sint occaecat cupidatat non proidentunt in cucia deserunt.</p></div></div>
  <div class="abs feature" style="left:99px;top:283px"><div class="feature-icon"><svg width="34" height="30" viewBox="0 0 28 24" fill="#fff"><circle cx="14" cy="7" r="3.5"/><circle cx="6" cy="9" r="2.6"/><circle cx="22" cy="9" r="2.6"/><path d="M8 20a6 6 0 0 1 12 0zM1 20a5 5 0 0 1 7-4.5 7 7 0 0 0-1.5 4.5zM27 20a5 5 0 0 0-7-4.5 7 7 0 0 1 1.5 4.5z"/></svg></div><div><h4>A Partner</h4><p>Excepteur sint occaecat cupidatat non proidentunt in cucia deserunt.</p></div></div>
  <div class="abs feature" style="left:451px;top:283px"><div class="feature-icon"><svg width="32" height="32" viewBox="0 0 24 24"><circle cx="12" cy="12" r="10" fill="#fff"/><path d="M7 12.5l3.5 3.5L17 9" stroke="var(--green)" stroke-width="2.4" fill="none"/></svg></div><div><h4>Selective</h4><p>Excepteur sint occaecat cupidatat non proidentunt in cucia deserunt.</p></div></div>
  <div class="abs feature" style="left:801px;top:283px"><div class="feature-icon"><svg width="30" height="30" viewBox="0 0 24 24"><path fill="#fff" d="M3 3h8l10 10-8 8L3 11zm4 2.5a1.5 1.5 0 1 0 0 3 1.5 1.5 0 0 0 0-3z"/></svg></div><div><h4>Competitive Rates &amp; Fees</h4><p>Excepteur sint occaecat cupidatat non proidentunt in cucia deserunt.</p></div></div>
</section>

<!-- blog -->
<h2 class="abs section-title" style="top:1980px">Blog <b>Articles</b></h2>
<article class="abs post" style="left:99px">
  <div class="abs post-photo" role="img" aria-label="Photo of hands reviewing printed charts and graphs" style="background:linear-gradient(135deg,#dfe3e6,#7f8a94)"></div>
  <div class="abs post-body"><h5>Circumstances Occur Inoila</h5><p>Sed ut perspiciatis unde omnis iste natus error sit voluptatem accusantium doloremque</p></div>
  <div class="abs post-rule"></div>
  <div class="abs post-meta"><b>▣ March 12,2017</b>|<b>6 comments</b>| 3 | 6</div>
</article>
<article class="abs post" style="left:439px">
  <div class="abs post-photo" role="img" aria-label="Photo of business people shaking hands at a table" style="background:linear-gradient(135deg,#5b6269,#c4c8cc)"></div>
  <div class="abs post-body"><h5>Eos Qui Ratione Voluptatem</h5><p>Sed ut perspiciatis unde omnis iste natus error sit voluptatem accusantium doloremque</p></div>
  <div class="abs post-rule"></div>
  <div class="abs post-meta"><b>▣ March 12,2017</b>|<b>6 comments</b>| 3 | 6</div>
</article>
<article class="abs post" style="left:779px">
  <div class="abs post-photo" role="img" aria-label="Photo of a desk with laptop, calculator, charts and coffee" style="background:linear-gradient(135deg,#8b7d6b,#d7d4cf)"></div>
  <div class="abs post-body"><h5>Neque Porro Quisquam Es</h5><p>Sed ut perspiciatis unde omnis iste natus error sit voluptatem accusantium doloremque</p></div>
  <div class="abs post-rule"></div>
  <div class="abs post-meta"><b>▣ March 12,2017</b>|<b>6 comments</b>| 3 | 6</div>
</article>

<!-- testimonials -->
<section class="abs clients"></section>
<h2 class="abs section-title" style="top:2574px">What Our <b>Clients Say</b></h2>
<p class="abs clients-sub">Lorem ipsum dolor sit amet consed do eiusmod tempor incididunt ut labore et dolore magna aliqua</p>
<div class="abs quote-box">
  <p class="abs quote-text">Sed ut perspiciatis unde omnis iste natus error sit voluptatem accusantium doloremque laudantium, totam rem aperiam, eaque ipsa quae ab illo inventore veritatis et quasi architecto beatae vitae dicta sunt explicabo. Nemo enim ipsam voluptatem quia voluptas sit aspernatur aut odit aut fugit, sed quia consequuntur magni dolores.</p>
  <div class="abs quote-author"><div class="avatar" role="img" aria-label="Client portrait"></div><div><h6>Architecto Beatae Vita</h6><span>Cepteur sint occaeca</span></div></div>
  <div class="abs quote-mark">”</div>
</div>
<div class="abs arrow-btn" style="left:140px"><svg width="8" height="12" viewBox="0 0 8 12"><path d="M6 1 1 6l5 5" stroke="#333" stroke-width="1.6" fill="none"/></svg></div>
<div class="abs arrow-btn" style="left:1028px"><svg width="8" height="12" viewBox="0 0 8 12"><path d="M2 1l5 5-5 5" stroke="#333" stroke-width="1.6" fill="none"/></svg></div>

<!-- footer -->
<footer class="abs footer" role="img" aria-label="Dark tinted photo of an office desk behind the footer"></footer>
<svg class="abs footer-cut" viewBox="0 0 1200 160" preserveAspectRatio="none">
  <polygon points="0,0 1200,0 1200,40 600,140 0,40" fill="var(--green)"/>
  <polygon points="0,0 1200,0 1200,28 600,124 0,28" fill="#eceeee"/>
</svg>
<div class="abs dots"><i class="on"></i><i></i><i></i></div>

<div class="abs f-col" style="left:104px;width:230px">
  <h4>Contact Us</h4>
  <ul class="f-list">
    <li><span>⌂</span><span>57 kjLorem ipsum dolor sit<br>amectetur aipiscing..</span></li>
    <li><span>▯</span><span>Phone : (555) - 210 - 4480</span></li>
    <li><span>✉</span><span>info@rtvfinance.example</span></li>
  </ul>
</div>
<div class="abs f-divider" style="left:372px"></div>
<div class="abs f-col" style="left:390px;width:170px">
  <h4>Quick Links</h4>
  <ul class="f-links"><li>Home</li><li>About Us</li><li>Loans</li><li>Resources</li><li>Contact Us</li></ul>
</div>
<div class="abs f-col" style="left:595px;width:300px">
  <h4 style="margin-bottom:16px">Sign Up Newsletter</h4>
  <p style="color:#fff;line-height:1.6">Ut enimad minima veniam, quis nostrum<br>aliquid cinima venonsequ.</p>
  <div class="f-input">Enter Email...</div>
  <div class="f-btn">SUBSCRIBE</div>
</div>
<div class="abs f-divider" style="left:915px"></div>
<div class="abs f-col" style="left:954px;width:160px">
  <h4>Soacial Media</h4>
  <div class="f-social"><i></i><span style="color:#fff">Friendspace</span></div>
  <div class="f-social"><i></i><span style="color:#fff">Linkwork</span></div>
</div>

<div class="abs f-rule"></div>
<div class="abs badges-label">Industry Membership Logos</div>
<div class="abs badge" style="left:332px;width:90px"></div>
<div class="abs badge" style="left:430px;width:178px"></div>
<div class="abs copyright">© copyright 2017 RTV Finance.All rights reserved.</div>
<div class="abs chat"><svg width="22" height="22" viewBox="0 0 24 24"><circle cx="12" cy="12" r="11" fill="#fff"/><path d="M7 8h10v6h-5l-3 3v-3H7z" fill="var(--green)"/></svg>LIVE CHAT</div>

</body>
</html>
```